Varnick Fundraising E-mail Campaign

I intend to use Constant Contact to send donors 4 separate e-mail messages with pictures, text and a hot link, “Give to Restore Marlowe.” E-mails will spaced about 3 days apart. I would like the first e-mail to go out on Monday, December 17. The e-mail campaign is part of a board match annual appeal fundraising campaign for a not for profit sleep away Christian camp. Our hope is to raise $40,000.00+

Target Market(s)

Members in Constant Contact list

Colors

Designer to choose colors to be used in the design.

Requirements
Must have
• E- mail recipient must be able to access hot link

```html
<!DOCTYPE html>
<html lang="en">
<head>
<meta charset="utf-8">
<title>Varnick Camp – Matching Challenge</title>
<link href="https://fonts.googleapis.com/css2?family=Arimo:wght@400;700&display=swap" rel="stylesheet">
<style>
:root{
  --page-bg:#adcc88;
  --paper:#ffffff;
  --alert-red:#e31e2a;
  --camp-green:#0b7a40;
  --frame-green:#a3c57e;
  --hill-green:#16a04a;
  --lake-blue:#22b0dc;
}
*{box-sizing:border-box;margin:0;padding:0}
html,body{width:1200px;height:979px;overflow:hidden;background:var(--page-bg);font-family:"Arimo",Arial,sans-serif}
.email{position:absolute;left:376px;top:0;width:448px;height:979px;background:var(--paper);color:var(--camp-green);overflow:hidden}
.donate-bar{height:24px;background:var(--alert-red);text-align:center}
.donate-bar a{color:#fff;font-weight:700;font-size:14px;line-height:24px;text-decoration:underline}
.brand{display:flex;align-items:center;justify-content:center;gap:8px;height:45px;margin-top:7px}
.brand-mark{width:14px;height:14px;background:var(--camp-green)}
.brand-name{font-size:22px;font-weight:400;color:var(--camp-green);letter-spacing:.5px}
.photo-frame{position:absolute;left:24px;width:400px;height:264px;border:5px solid var(--frame-green)}
.photo-frame.first{top:77px}
.photo-frame.second{top:441px}
.photo{width:100%;height:100%}
.photo.campers{background:linear-gradient(135deg,#5a3b28,#8a6048 45%,#e58a6c 70%,#3a8ec8)}
.photo.hike{background:linear-gradient(160deg,#3e7a2a,#6fae3c 50%,#2c5a1e)}
.appeal{position:absolute;top:366px;width:100%;text-align:center;font-weight:700;font-size:12.5px;line-height:19px;letter-spacing:.2px}
.reminder{position:absolute;top:717px;width:100%;height:49px;background:var(--alert-red);color:#fff;text-align:center;font-weight:700;font-size:12.5px;line-height:49px}
.link{position:absolute;top:779px;width:100%;text-align:center;font-size:14.5px;line-height:17px}
.link a{color:var(--camp-green);text-decoration:underline}
.contact{position:absolute;left:8px;top:836px;font-size:9.5px;line-height:13.2px}
.scenery{position:absolute;left:0;bottom:0;width:448px;height:80px;background:linear-gradient(180deg,var(--hill-green) 0%,#0e8a44 55%,var(--lake-blue) 100%)}
</style>
</head>
<body>
<div class="email">
  <div class="donate-bar"><a href="http://varnickcamp.org/support">DONATE NOW</a></div>
  <div class="brand"><span class="brand-mark"></span><span class="brand-name">VARNICK</span></div>

  <div class="photo-frame first"><div class="photo campers" role="img" aria-label="Two smiling campers in a rustic wooden cabin"></div></div>

  <p class="appeal">Last chance to take advantage of the matching challenge!<br>Double your impact!<br>Every gift is matched dollar for dollar up to 20,000!</p>

  <div class="photo-frame second"><div class="photo hike" role="img" aria-label="Campers in climbing harnesses hiking a forest trail"></div></div>

  <div class="reminder">If you haven’t done so, please donate today.</div>

  <p class="link"><a href="http://varnickcamp.org/support">Visit http://varnickcamp.org/support and click on<br>"Restore Marlowe</a></p>

  <div class="contact">
    Contact:<br>
    14 Marlowe Lake Road Varnick, NY 12000<br>
    Phone: 555-014-2273 Fax: 555-014-2290<br>
    E-Mail: office@varnickcamp.org
  </div>

  <div class="scenery" role="img" aria-label="Illustration of a tree on green hills beside a lake"></div>
</div>
</body>
</html>
```